Brightlane Electrical and Air conditioning services needs Designer Van Signage.

Brightlane Electrical and Air conditioning company needs a Van signage designed to give customers a professional image of the business. Attached are some sample design that we will be interested in. Do not need full van wrap, Back Half should be ok.

Industry/Entity Type

Electrical, Air conditioning, & Plumbing

Requirements
Must have
• 24 hour emergency service. Electrical , Air conditioning & Plumbing ideas. Please show all around van. front back and 2 sides.
Nice to have
• Please use mobile number: 0437512806, email: info@brightlaneelectrical.example.com.au, Web: www.brightlaneelectrical.example.com.au.
Should not have
• Full van wrap

```html
<!DOCTYPE html>
<html lang="en">
<head>
<meta charset="utf-8">
<title>Brightlane Van Signage</title>
<link rel="stylesheet" href="https://fonts.googleapis.com/css2?family=Montserrat:wght@600;700;800&family=Ubuntu:wght@500;700&family=Oswald:wght@600;700&display=swap">
<style>
  :root {
    --bg: #f5f5f5;
    --panel: #ffffff;
    --panel-edge: #e2e2e2;
    --orange: #f0914f;
    --brand-orange: #ee8a3c;
    --red: #e8505b;
    --blue: #2b6cb0;
    --cream: #fbf0e8;
    --white: #ffffff;
    --ink: #333333;
  }
  html, body { margin: 0; padding: 0; overflow: hidden; }
  body { width: 1200px; height: 1151px; background: var(--bg); }
  .signage { display: block; width: 1200px; height: 1151px; }
  .panel-base { fill: var(--panel); stroke: var(--panel-edge); stroke-width: 1.5; }
  .fill-orange { fill: var(--orange); }
  .fill-red { fill: var(--red); }
  .fill-blue { fill: var(--blue); }
  .fill-cream { fill: var(--cream); }
  .service-list { font-family: "Montserrat", sans-serif; font-weight: 800; fill: var(--blue); }
  .bullet { fill: var(--red); }
  .brand-name { font-family: "Ubuntu", sans-serif; font-weight: 500; fill: var(--brand-orange); }
  .brand-tagline { font-family: "Ubuntu", sans-serif; font-weight: 700; font-size: 11.5px; }
  .tag-red { fill: var(--red); }
  .tag-blue { fill: var(--blue); }
  .tag-orange { fill: var(--brand-orange); }
  .web-pill { fill: none; stroke: var(--blue); stroke-width: 1.2; }
  .web-text { font-family: "Montserrat", sans-serif; font-weight: 700; font-size: 8.2px; fill: var(--blue); }
  .email-text { font-family: "Montserrat", sans-serif; font-weight: 600; font-size: 8.6px; fill: var(--ink); }
  .phone-text { font-family: "Ubuntu", sans-serif; font-weight: 500; fill: var(--white); }
  .strap { font-family: "Montserrat", sans-serif; font-weight: 700; font-size: 8px; fill: var(--blue); }
  .hours { font-family: "Oswald", sans-serif; font-weight: 700; fill: var(--blue); }
  .emergency { font-family: "Oswald", sans-serif; font-weight: 600; fill: var(--blue); }
  .services-label { font-family: "Oswald", sans-serif; font-weight: 600; fill: var(--white); }
  .licence { font-family: "Montserrat", sans-serif; font-weight: 600; font-size: 4.6px; fill: var(--ink); }
  .icon-line { fill: none; stroke: var(--white); stroke-width: 1.2; stroke-linecap: round; stroke-linejoin: round; }
</style>
</head>
<body>
<svg class="signage" viewBox="0 0 1200 1151" xmlns="http://www.w3.org/2000/svg" aria-label="Brightlane van signage: side panel and two rear door options">

  <g class="side-panel">
    <rect class="panel-base" x="190" y="165" width="925" height="310" rx="30"/>
    <path class="fill-orange" d="M1095,205 C1000,235 920,320 840,445 L845,422 L1095,422 Z"/>
    <path class="fill-blue" d="M580,428 L826,428 L838,470 L416,470 L416,457 L566,457 Z"/>
    <path class="fill-red" d="M752,390 L790,400 L833,440 C900,330 990,250 1095,205 L1095,232 C1000,272 920,350 838,470 Z"/>

    <g class="service-list" font-size="16">
      <rect class="bullet" x="874" y="205" width="4" height="4"/><text x="883" y="216">ELECTRICAL</text>
      <rect class="bullet" x="874" y="232" width="4" height="4"/><text x="883" y="243">AIR CONDITIONING</text>
      <rect class="bullet" x="874" y="258" width="4" height="4"/><text x="883" y="269">PLUMBING</text>
      <rect class="bullet" x="874" y="282" width="4" height="4"/><text x="883" y="293">CCTV SECURITY</text>
    </g>

    <g class="emergency-badge">
      <text class="hours" x="944" y="369" font-size="37">24/7</text>
      <text class="emergency" x="1013" y="357" font-size="15">Emergency</text>
      <rect class="fill-red" x="1014" y="360" width="41" height="11"/>
      <text class="services-label" x="1017" y="369.5" font-size="8.5">SERVICES</text>
    </g>

    <g class="brand-block">
      <circle class="fill-orange" cx="727" cy="270" r="36"/>
      <text class="brand-name" x="629" y="358" font-size="40" textLength="203">Brightlane</text>
      <text class="brand-tagline" x="628" y="373">
        <tspan class="tag-red">Electrical</tspan><tspan class="tag-blue"> | Air Conditioning </tspan><tspan class="tag-orange">| Plumbing</tspan>
      </text>
      <rect class="web-pill" x="631" y="383" width="192" height="20" rx="10"/>
      <text class="web-text" x="727" y="396" text-anchor="middle">www.brightlaneelectrical.example.com.au</text>
      <g class="email">
        <rect x="646" y="410" width="8" height="6" fill="none" stroke="#2b6cb0" stroke-width="1"/>
        <path d="M646,410 L650,413.5 L654,410" fill="none" stroke="#2b6cb0" stroke-width="1"/>
        <text class="email-text" x="657" y="418">info@brightlaneelectrical.example.com.au</text>
      </g>
      <g class="phone">
        <circle class="fill-orange" cx="640" cy="445" r="9"/>
        <path class="icon-line" d="M636.5,441 q1,-1 2,0 l1,1.5 q0.5,1 -0.5,1.6 q1,2 3,3 q0.6,-1 1.6,-0.5 l1.5,1 q1,1 0,2 q-2,1.5 -5,-0.5 q-3,-2 -4,-5 q-0.5,-2 0.4,-3.1 Z"/>
        <text class="phone-text" x="654" y="454" font-size="24">0437512806</text>
      </g>
    </g>

    <g class="door-block">
      <circle class="fill-orange" cx="495" cy="361" r="11"/>
      <text class="brand-name" x="460" y="395" font-size="16">Brightlane</text>
      <text class="strap" x="443" y="425">Installation, Service, Repairs</text>
      <text class="strap" x="443" y="435">and Maintenance.</text>
    </g>
  </g>

  <g class="rear-panel rear-orange" transform="translate(143,797)">
    <rect class="fill-orange" x="0" y="0" width="324" height="150" rx="6"/>
    <path class="fill-cream" d="M315,0 L318,0 Q324,0 324,6 L324,144 Q324,150 318,150 L165,150 C210,85 260,30 315,0 Z"/>
    <path class="fill-red" d="M90,92 L124,100 L146,128 C190,70 240,25 295,0 L315,0 C260,30 210,85 165,150 L142,150 Z"/>
    <g class="service-list" font-size="8.5">
      <text x="10" y="56">• ELECTRICAL</text>
      <text x="10" y="70">• AIR CONDITIONING</text>
      <text x="10" y="84">• PLUMBING</text>
      <text x="10" y="97">• CCTV SECURITY</text>
    </g>
    <text class="licence" x="18" y="119">Electrical License Number - PGE482017</text>
    <path class="fill-red" d="M12,124 L126,124 L119,139 L12,139 Z"/>
    <circle class="fill-blue" cx="15" cy="131.5" r="7.5"/>
    <path class="icon-line" d="M12.3,128.3 q0.8,-0.8 1.6,0 l0.8,1.2 q0.4,0.8 -0.4,1.3 q0.8,1.6 2.4,2.4 q0.5,-0.8 1.3,-0.4 l1.2,0.8 q0.8,0.8 0,1.6 q-1.6,1.2 -4,-0.4 q-2.4,-1.6 -3.2,-4 q-0.4,-1.6 0.3,-2.5 Z"/>
    <text class="phone-text" x="28" y="137.5" font-size="15">0437512806</text>
    <text class="hours" x="190" y="141" font-size="30">24/7</text>
    <text class="emergency" x="255" y="121" font-size="13">Emergency</text>
    <rect class="fill-red" x="256" y="124" width="37" height="10"/>
    <text class="services-label" x="258.5" y="132.5" font-size="8">SERVICES</text>
  </g>

  <g class="rear-panel rear-white" transform="translate(741,797)">
    <rect class="panel-base" x="0" y="0" width="324" height="150" rx="6"/>
    <path class="fill-orange" d="M315,0 L318,0 Q324,0 324,6 L324,144 Q324,150 318,150 L165,150 C210,85 260,30 315,0 Z"/>
    <path class="fill-red" d="M90,92 L124,100 L146,128 C190,70 240,25 295,0 L315,0 C260,30 210,85 165,150 L142,150 Z"/>
    <g class="service-list" font-size="8.5">
      <text x="10" y="56">• ELECTRICAL</text>
      <text x="10" y="70">• AIR CONDITIONING</text>
      <text x="10" y="84">• PLUMBING</text>
      <text x="10" y="97">• CCTV SECURITY</text>
    </g>
    <text class="licence" x="18" y="119">Electrical License Number - PGE482017</text>
    <path class="fill-red" d="M12,124 L126,124 L119,139 L12,139 Z"/>
    <circle class="fill-blue" cx="15" cy="131.5" r="7.5"/>
    <path class="icon-line" d="M12.3,128.3 q0.8,-0.8 1.6,0 l0.8,1.2 q0.4,0.8 -0.4,1.3 q0.8,1.6 2.4,2.4 q0.5,-0.8 1.3,-0.4 l1.2,0.8 q0.8,0.8 0,1.6 q-1.6,1.2 -4,-0.4 q-2.4,-1.6 -3.2,-4 q-0.4,-1.6 0.3,-2.5 Z"/>
    <text class="phone-text" x="28" y="137.5" font-size="15">0437512806</text>
    <text class="hours" x="190" y="141" font-size="30">24/7</text>
    <text class="emergency" x="255" y="121" font-size="13">Emergency</text>
    <rect class="fill-red" x="256" y="124" width="37" height="10"/>
    <text class="services-label" x="258.5" y="132.5" font-size="8">SERVICES</text>
  </g>
</svg>
</body>
</html>
```